Colin Vardek Business card

Hey there, I’m hoping to have a business card designed. I’m in Real estate and just switched to a new Brokerage called: The Harbourline Property Group

The back could just be the company name maybe or whatever looks good!

I’ve attached some logos of our company and some cards my buddy had done up.

On the card:
Colin Vardek
colinvardek@mailora.com
587-412-9065
colinvardek.ca

Target Market(s)

Home buyers and sellers

Industry/Entity Type

Real Estate

Contact Information for Business Card

just looking for a cool and modern design with my picture on it. I like the idea of Black and red being used.

Requirements
Must have
• all the details provided. I'm open to anything. Just want a professional looking card.

```html
<!DOCTYPE html>
<html lang="en">
<head>
<meta charset="UTF-8">
<title>Colin Vardek Business Card</title>
<link href="https://fonts.googleapis.com/css2?family=Montserrat:wght@500;600&family=Poppins:wght@400&display=swap" rel="stylesheet">
<style>
  :root {
    --backdrop: #0d0d0f;
    --card: #232227;
    --red: #e0193f;
    --white: #f2f2f2;
    --grey: #8c8c90;
    --photo-light: #dcdcdf;
    --photo-dark: #3a3a40;
  }
  * { box-sizing: border-box; margin: 0; padding: 0; }
  html, body {
    width: 1200px; height: 1015px; overflow: hidden;
    background: var(--backdrop);
  }
  .stage { position: relative; width: 1200px; height: 1015px; }
  .card {
    position: absolute;
    width: 560px; height: 320px;
    background: var(--card);
    border-bottom: 4px solid var(--red);
    border-left: 2px solid var(--red);
    box-shadow: 0 18px 40px rgba(0,0,0,.6);
    overflow: hidden;
  }
  .card--front { left: 110px; top: 140px; }
  .card--back { left: 530px; top: 555px; }

  .brand {
    font-family: "Montserrat", sans-serif;
    font-weight: 600;
    letter-spacing: .04em;
    text-transform: uppercase;
  }
  .front-brand {
    position: absolute; inset: 0;
    display: flex; align-items: center; justify-content: center; gap: 14px;
    color: var(--red); font-size: 26px; line-height: 1.25; text-align: left;
  }
  .front-brand .mark { width: 18px; height: 18px; background: var(--red); flex: none; }

  .agent-name {
    position: absolute; right: 28px; top: 34px;
    font-family: "Montserrat", sans-serif; font-weight: 500;
    font-size: 22px; letter-spacing: .06em; text-transform: uppercase;
    color: var(--red);
  }
  .name-tab {
    position: absolute; right: 0; top: 30px;
    width: 12px; height: 34px; background: var(--red);
  }
  .portrait {
    position: absolute; left: 36px; top: 40px;
    width: 230px; height: 170px; border-radius: 14px;
    background: linear-gradient(160deg, var(--photo-light) 0%, #b9b9be 55%, var(--photo-dark) 100%);
  }
  .contacts {
    position: absolute; left: 36px; bottom: 26px;
    list-style: none;
    font-family: "Poppins", sans-serif; font-size: 16px; color: var(--white);
  }
  .contacts li { display: flex; align-items: center; gap: 10px; line-height: 26px; }
  .contacts svg { width: 16px; height: 16px; flex: none; }
  .back-brand {
    position: absolute; right: 28px; bottom: 34px;
    color: var(--grey); font-size: 17px; text-align: right; line-height: 1.3;
  }
</style>
</head>
<body>
<main class="stage">
  <section class="card card--front" aria-label="Card front">
    <div class="front-brand brand">
      <span class="mark"></span>
      <span>The Harbourline<br>Property Group</span>
    </div>
  </section>

  <section class="card card--back" aria-label="Card back">
    <div class="portrait" role="img" aria-label="Portrait photo of Colin Vardek"></div>
    <h1 class="agent-name">Colin Vardek</h1>
    <span class="name-tab"></span>
    <ul class="contacts">
      <li>
        <svg viewBox="0 0 24 24" fill="var(--red)"><path d="M6.6 10.8a15.1 15.1 0 0 0 6.6 6.6l2.2-2.2a1 1 0 0 1 1-.25 11.4 11.4 0 0 0 3.6.57 1 1 0 0 1 1 1V20a1 1 0 0 1-1 1A17 17 0 0 1 3 4a1 1 0 0 1 1-1h3.5a1 1 0 0 1 1 1c0 1.25.2 2.45.57 3.6a1 1 0 0 1-.25 1z"/></svg>
        587-412-9065
      </li>
      <li>
        <svg viewBox="0 0 24 24" fill="var(--red)"><path d="M2 5h20v14H2z M2 5l10 8 10-8" stroke="var(--card)" stroke-width="1.5"/></svg>
        colinvardek@mailora.com
      </li>
      <li>
        <svg viewBox="0 0 24 24" fill="none" stroke="var(--red)" stroke-width="2"><circle cx="12" cy="12" r="9"/><path d="M3 12h18M12 3c3 3 3 15 0 18M12 3c-3 3-3 15 0 18"/></svg>
        colinvardek.ca
      </li>
    </ul>
    <div class="back-brand brand">The Harbourline<br>Property Group</div>
  </section>
</main>
</body>
</html>
```